Business Card for Coastal Tundrabridge Advisory

We need a business card for Coastal Tundrabridge Advisory. The company website address is provided below. The company logo is attached. We provide specialized permafrost services to the mining, transportation, and oil & gas industries. The card should be prepared for:
Matthias Korhonen, PhD.
Coastal Tundrabridge Advisory
PO Box 418259
Quillwater, Alaska 99642
Direct: +1-907-555-0143
Email: mkorhonen@tundrabridgeadvisory.example
Website: www.coastaltundrabridgeadvisory.example

```html
<!DOCTYPE html>
<html lang="en">
<head>
<meta charset="utf-8">
<title>Coastal Tundrabridge Advisory — Business Card</title>
<link href="https://fonts.googleapis.com/css2?family=Lato:wght@400;700&display=swap" rel="stylesheet">
<style>
  :root {
    --page-bg: #1b1c1f;
    --card-bg: #111821;
    --accent-bar: #3a4450;
    --text-main: #ffffff;
    --text-soft: #a3abb5;
    --divider: #3c4651;
  }
  * { margin: 0; padding: 0; box-sizing: border-box; }
  html, body {
    width: 1200px; height: 952px; overflow: hidden;
    background: var(--page-bg);
    font-family: "Lato", Arial, sans-serif;
    color: var(--text-main);
  }
  .canvas {
    position: relative; width: 1200px; height: 952px;
    display: flex; flex-direction: column; align-items: center; justify-content: center; gap: 50px;
  }
  .card {
    position: relative; width: 700px; height: 400px;
    background: var(--card-bg);
    overflow: hidden;
  }

  /* Front */
  .card-front { display: flex; align-items: center; justify-content: center; }
  .brand-name {
    font-weight: 700; text-transform: uppercase; text-align: center;
    letter-spacing: 0.12em; line-height: 1.2; color: var(--text-main);
  }
  .card-front .brand-name { font-size: 34px; }

  /* Back */
  .accent-bar { position: absolute; width: 16px; height: 140px; background: var(--accent-bar); }
  .accent-bar.top-left { left: 0; top: 0; }
  .accent-bar.bottom-right { right: 0; bottom: 0; }

  .card-back .brand-block {
    position: absolute; left: 56px; top: 108px; width: 260px;
  }
  .card-back .brand-name { font-size: 21px; text-align: left; letter-spacing: 0.1em; }

  .postal-address {
    position: absolute; left: 56px; top: 262px;
    font-size: 15px; letter-spacing: 0.14em; color: var(--text-main);
  }

  .column-divider {
    position: absolute; left: 338px; top: 90px; width: 1px; height: 150px;
    background: var(--divider);
  }

  .contact-block { position: absolute; left: 360px; top: 110px; width: 320px; }
  .person-name { font-size: 19px; font-weight: 700; text-transform: uppercase; letter-spacing: 0.02em; }
  .person-company { font-size: 14px; color: var(--text-soft); margin-top: 2px; }
  .contact-list { list-style: none; margin-top: 14px; }
  .contact-list li {
    display: flex; align-items: center; gap: 8px;
    font-size: 13px; color: var(--text-soft); line-height: 24px; white-space: nowrap;
  }
  .contact-list svg { width: 13px; height: 13px; flex: none; fill: var(--text-main); }
</style>
</head>
<body>
<main class="canvas">
  <section class="card card-front" aria-label="Card front">
    <div class="brand-name">Coastal Tundrabridge<br>Advisory</div>
  </section>

  <section class="card card-back" aria-label="Card back">
    <span class="accent-bar top-left"></span>
    <span class="accent-bar bottom-right"></span>

    <div class="brand-block">
      <div class="brand-name">Coastal Tundrabridge<br>Advisory</div>
    </div>

    <p class="postal-address">PO Box 418259, Quillwater, Alaska 99642</p>

    <span class="column-divider"></span>

    <div class="contact-block">
      <h1 class="person-name">Matthias Korhonen, PhD</h1>
      <p class="person-company">Coastal Tundrabridge Advisory</p>
      <ul class="contact-list">
        <li>
          <svg viewBox="0 0 16 16" aria-hidden="true"><path d="M3.6 1.2l2.3 2.6-1.3 1.9c.9 2 2.6 3.7 4.6 4.6l1.9-1.3 2.6 2.3-1.3 2.3C7 13.5 2.5 9 1.3 3.3z"/></svg>
          +1-907-555-0143
        </li>
        <li>
          <svg viewBox="0 0 16 16" aria-hidden="true"><path d="M1 3h14v1.2L8 9 1 4.2zM1 5.8l7 4.8 7-4.8V13H1z"/></svg>
          mkorhonen@tundrabridgeadvisory.example
        </li>
        <li>
          <svg viewBox="0 0 16 16" aria-hidden="true"><path d="M8 1a7 7 0 100 14A7 7 0 008 1zm0 1.5c.8 0 1.7 1.6 2 4H6c.3-2.4 1.2-4 2-4zM2.6 6.5h2c-.1.5-.1 1-.1 1.5s0 1 .1 1.5h-2a5.5 5.5 0 010-3zm3.4 3h4c-.3 2.4-1.2 4-2 4s-1.7-1.6-2-4zm5.4 0c.1-.5.1-1 .1-1.5s0-1-.1-1.5h2a5.5 5.5 0 010 3z"/></svg>
          www.coastaltundrabridgeadvisory.example
        </li>
      </ul>
    </div>
  </section>
</main>
</body>
</html>
```